Board to put on a meditation centre - Lantern Grove

I need a board design for a new meditation centre based in Oslo which offers free courses in meditation and self-empowerment. The size of the board is width 374cm x height 104cm.  The name of the meditation centre together with subtitles should be on the board but also some elegant decoration that matches the theme (lantern grove/meditation).
Here is the website of the meditation centre to give you a feeling of it: https://kvitfjellsenteret.no/
Good if you can use a blue color close to this one: rgb(37, 180, 193) as well as some brown/golden color (similar to the palette on the website).
On the board it should say:
Kveldens lund (in big letters, the rest is subtitles)
Meditasjon & Spirituell visdom
Kurs - Retreat - Dialog
kvitfjellsenteret.no
The design should be very elegant and beautiful and the feeling should be of "A Lantern Grove". A logo is here attached and should be used but I need to get a better quality version of it, will upload that as soon as possible.

```html
<!DOCTYPE html>
<html lang="no">
<head>
<meta charset="utf-8">
<title>Kveldens lund – skilt</title>
<link href="https://fonts.googleapis.com/css2?family=Antonio:wght@100;200&family=Lato:wght@300;400&display=swap" rel="stylesheet">
<style>
  :root {
    --teal: #2ab3c2;
    --teal-soft: #8fd3dc;
    --cream: #f4f1ea;
    --mist: #e4f1f2;
    --peach: #f2c9ad;
    --coral: #ee8f6c;
  }
  * { margin: 0; padding: 0; box-sizing: border-box; }
  html, body { width: 1200px; height: 334px; overflow: hidden; background: var(--cream); }
  .board {
    position: relative;
    width: 1200px;
    height: 334px;
    overflow: hidden;
    color: var(--teal);
    font-family: "Lato", sans-serif;
  }
  .backdrop {
    position: absolute;
    inset: 0;
    background:
      radial-gradient(ellipse 140px 90px at 250px 270px, rgba(238,143,108,0.45), transparent 70%),
      radial-gradient(ellipse 90px 60px at 200px 120px, rgba(120,200,210,0.45), transparent 70%),
      radial-gradient(ellipse 120px 110px at 500px 90px, rgba(90,200,215,0.5), transparent 70%),
      radial-gradient(ellipse 80px 40px at 220px 25px, rgba(242,170,120,0.4), transparent 70%),
      radial-gradient(ellipse 120px 60px at 1110px 70px, rgba(242,190,150,0.4), transparent 70%),
      radial-gradient(ellipse 420px 220px at 650px 150px, rgba(200,232,236,0.8), transparent 75%),
      linear-gradient(90deg, var(--cream) 0%, var(--mist) 45%, #eef4f2 75%, var(--cream) 100%);
  }
  .title {
    position: absolute;
    left: 392px;
    top: 138px;
    font-family: "Antonio", sans-serif;
    font-weight: 100;
    font-size: 64px;
    line-height: 1;
    letter-spacing: 19px;
    white-space: nowrap;
  }
  .subtitle {
    position: absolute;
    left: 458px;
    top: 210px;
    font-weight: 300;
    font-size: 21px;
    letter-spacing: 0.2px;
    white-space: nowrap;
  }
  .offerings {
    position: absolute;
    left: 417px;
    top: 284px;
    font-weight: 400;
    font-size: 28px;
    letter-spacing: 7px;
    white-space: nowrap;
  }
  .website {
    position: absolute;
    left: 33px;
    top: 297px;
    font-weight: 300;
    font-size: 14px;
    letter-spacing: 0.3px;
  }
  .centre-name {
    position: absolute;
    right: 16px;
    top: 258px;
    display: flex;
    flex-direction: column;
    align-items: center;
    gap: 6px;
    font-weight: 400;
    font-size: 11px;
    letter-spacing: 1px;
    color: var(--teal);
  }
  .centre-name .dot {
    width: 14px;
    height: 14px;
    border-radius: 50%;
    background: var(--teal);
  }
</style>
</head>
<body>
  <div class="board">
    <div class="backdrop" role="img" aria-label="Soft marbled ink background in pale aqua, cream and coral tones"></div>
    <h1 class="title">KVELDENS LUND</h1>
    <p class="subtitle">Meditasjon &amp; Spirituel Visdom</p>
    <p class="offerings">KURS&nbsp; - &nbsp;RETREAT&nbsp; -DIALOG</p>
    <p class="website">kvitfjellsenteret.no</p>
    <div class="centre-name">
      <span class="dot"></span>
      <span>Kveldens lund</span>
    </div>
  </div>
</body>
</html>
```